I have a business that exists already (Linden Conservatory of Music) that we offer music lessons to all instruments. I recently opened a smaller version called CHORDS by Linden that will only teach piano lessons. What I'm looking for now is a 3 page Website on word press. After I choose the design I like I want to be able to take over the website and bring it to our hosting company. We want full control of it and our team will take over. The reason I'm doing this is to have other visions and ideas from others. The first page will be about the company and our message/vision. Second page about the piano lessons. The third will be about franchising this concept "Chords by Linden" Attached are 3 Logos . Please refer to our existing website www.lindenmusicconservatory.example to look at our piano page and franchising page. Please feel free to message me if you need more info. Thanks
Please note I do not want the new website (Chords by Linden) To look like the other Website (Linden Conservatory of Music) Fresh new look. I do not want the colours red or using the Red logo. I only provided it so that you have an Idea of What the other business looks like and that you can take the piano content and franchise content off of it. Chords by Linden is smaller concept and only piano lessons.
Thanks
Only Piano lessons for all students
3 page

```html
<!DOCTYPE html>
<html lang="en">
<head>
<meta charset="utf-8">
<title>CHORDS by Linden – Piano Lessons</title>
<link rel="stylesheet" href="https://fonts.googleapis.com/css2?family=Cinzel:wght@400;500&family=Crimson+Pro:ital,wght@0,400;1,400&family=Great+Vibes&family=Montserrat:wght@400;500&display=swap">
<style>
:root{
  --black:#0b0b0b;
  --gold:#e8c35f;
  --gold-soft:#ecc967;
  --blue:#2196f3;
  --ink:#1c1c1c;
  --text:#333;
  --panel:#f2f2f2;
  --white:#fff;
  --slate:#4a4a4a;
}
*{box-sizing:border-box;margin:0;padding:0}
html,body{width:1200px;height:3176px;overflow:hidden}
body{position:relative;background:var(--white);font-family:"Crimson Pro",Georgia,serif;color:var(--text)}
h1,h2,h3{font-weight:400}
.abs{position:absolute}
.btn{display:inline-flex;align-items:center;justify-content:center;font-family:"Cinzel",serif;font-size:14px;letter-spacing:.5px}
.btn.abs{position:absolute}
.btn-gold{background:var(--gold);color:var(--ink)}
.btn-blue{background:var(--blue);color:var(--white);font-size:16px}
.rule{height:2px;width:32px}
.rule.abs{position:absolute}
.rule-blue{background:var(--blue)}
.rule-gold{background:var(--gold)}

/* hero */
.hero{left:0;top:0;width:1200px;height:600px;background:radial-gradient(ellipse at 82% 35%,#c98a4a 0%,#6b3b1e 22%,#2a1a12 45%,#0d0c0d 75%);border-bottom:2px solid #8a6b2a}
.site-header{left:0;top:0;width:1200px;height:78px;background:rgba(0,0,0,.82)}
.brand{left:146px;top:14px;font-family:"Cinzel",serif;font-size:30px;color:var(--white);line-height:1}
.brand small{display:block;font-size:13px;letter-spacing:1px;margin-top:4px}
.nav{left:460px;top:32px;font-family:"Cinzel",serif;font-size:12.5px;color:var(--white)}
.nav span{position:absolute;white-space:nowrap}
.nav .active{color:var(--gold)}
.nav-divider{left:922px;top:20px;width:1px;height:34px;background:#777}
.social{top:34px;width:9px;height:9px;border-radius:50%;background:var(--gold)}
.welcome{left:141px;top:215px;font-family:"Great Vibes",cursive;font-size:76px;color:var(--gold);line-height:1}
.hero-title{left:141px;top:302px;font-family:"Cinzel",serif;font-size:52px;color:var(--white);letter-spacing:1px}

.section-title{font-family:"Cinzel",serif;color:var(--ink)}

/* about */
.about{left:150px;top:645px;width:900px;display:flex;flex-direction:column;align-items:center;text-align:center}
.about-title{font-size:30px;line-height:40px}
.about .rule{margin:8px 0 14px}
.about-sub{font-style:italic;font-size:23px;color:var(--ink);margin-bottom:6px}
.about-copy{font-size:15px;line-height:25.5px}
.about-copy p{margin-bottom:8px}
.about .btn{width:155px;height:35px;margin-top:10px}

/* vision */
.vision-photo{left:0;top:998px;width:596px;height:543px;background:linear-gradient(120deg,#d9d2c8 0%,#f3f1ee 40%,#e7e3df 70%,#bfb6ab 100%)}
.vision-panel{left:596px;top:998px;width:604px;height:543px;background:var(--panel)}
.blue-bar{position:absolute;width:7px;background:var(--blue)}
.vision{left:635px;top:1118px;width:430px}
.vision-title{font-size:32px;line-height:40px}
.vision .rule{margin:14px 0 12px}
.vision-copy{font-size:15px;line-height:25.5px}
.vision-copy p{margin-bottom:6px}
.vision .btn{width:183px;height:33px;margin-top:10px}

/* programs */
.programs{left:142px;top:1668px;width:440px}
.programs-title{font-size:25px;line-height:36px}
.programs .rule{margin:14px 0 14px}
.programs-list{list-style:none;font-size:15px;line-height:25.5px}
.programs-list li{position:relative;padding-left:26px;margin-bottom:7px}
.programs-list svg{position:absolute;left:0;top:7px}
.programs .btn{width:183px;height:33px;margin-top:4px}
.programs-photo{left:604px;top:1620px;width:596px;height:543px;background:linear-gradient(135deg,#6e5f52 0%,#a89a8a 35%,#3f342d 65%,#c7a98f 100%)}

/* franchise */
.franchise{left:0;top:2236px;width:1200px;height:269px;background:linear-gradient(180deg,#ececec 0%,#f4f4f4 50%,#e6e6e6 100%)}
.franchise-title{left:0;top:2298px;width:1200px;text-align:center;font-size:32px}
.franchise-sub{left:0;top:2358px;width:1200px;text-align:center;font-family:"Montserrat",sans-serif;font-size:15px;letter-spacing:.5px;color:var(--text)}

/* booking */
.booking-top{left:0;top:2505px;width:1200px;height:180px;background:linear-gradient(180deg,#1a1a1a 0%,#3a3a3a 100%)}
.booking-bottom{left:0;top:2685px;width:1200px;height:300px;background:var(--slate)}
.booking-title{left:0;top:2568px;width:1200px;text-align:center;font-family:"Cinzel",serif;font-size:25px;color:var(--white)}
.form-card{left:141px;top:2642px;width:918px;height:270px;background:var(--white)}
.field{position:absolute;background:var(--white);box-shadow:0 1px 5px rgba(0,0,0,.14);font-family:"Montserrat",sans-serif;font-size:12px;color:#666;padding:12px 14px}

/* contact strip */
.contact-strip{left:0;top:2985px;width:1200px;height:191px;background:var(--gold-soft)}
.contact-item{position:absolute;top:3040px;width:300px;text-align:center;color:var(--ink)}
.contact-item svg{display:block;margin:0 auto 12px}
.contact-label{font-family:"Cinzel",serif;font-size:14.5px}
.contact-text{font-family:"Montserrat",sans-serif;font-size:12.5px;line-height:20px}
</style>
</head>
<body>

<section class="abs hero" role="img" aria-label="Photo of a young woman playing a grand piano on a dimly lit stage"></section>
<header class="abs site-header">
  <div class="abs brand">CHORDS<small>by Linden</small></div>
  <nav class="abs nav">
    <span class="active" style="left:0">HOME</span>
    <span style="left:84px">PIANO LESSONS</span>
    <span style="left:224px">FRANCHISING</span>
    <span style="left:351px">CONTACT US</span>
  </nav>
  <div class="abs nav-divider"></div>
  <span class="abs social" style="left:953px"></span>
  <span class="abs social" style="left:983px"></span>
  <span class="abs social" style="left:1017px"></span>
  <span class="abs social" style="left:1049px"></span>
</header>
<div class="abs welcome">Welcome to</div>
<h1 class="abs hero-title">CHORDS BY LINDEN</h1>
<div class="btn abs btn-gold" style="left:141px;top:390px;width:115px;height:34px">READ MORE</div>

<section class="abs about">
  <h2 class="section-title about-title">ABOUT CHORDS by Linden</h2>
  <div class="rule rule-blue"></div>
  <h3 class="about-sub">Playing the Piano</h3>
  <div class="about-copy">
    <p>When you think of a piano, you probably envision black and white keys but the piano is more than those harmonious sounds created by the player. The versatility and the musicianship instilled into the player &nbsp;from those keys is the true magic that comes from playing piano!</p>
    <p>Starting from the grassroots, experience different methods and styles of playing piano. To mark the milestones of progression, engage in one of Linden’s many unique performance opportunities like annual festival competitions, recitals or our examinations (Linden &amp; NMB). Penultimately, at the end of the journey, join our elite teaching program to bring the same joy of learning the piano to another student.</p>
  </div>
  <div class="btn btn-blue">Read More</div>
</section>

<div class="abs vision-photo" role="img" aria-label="Photo of a teacher guiding a young student at a white grand piano"></div>
<div class="abs vision-panel"></div>
<div class="blue-bar" style="left:596px;top:1093px;height:352px"></div>
<section class="abs vision">
  <h2 class="section-title vision-title">OUR VISION</h2>
  <div class="rule rule-blue"></div>
  <div class="vision-copy">
    <p>Our Mission is Lorem ipsum dolor sit amet, consectetuer adipiscig elit, sed diama nonummy nibh euismod tincidunt ut laoreet dolore magna aliquam erat volutpat. Ut wisi enim ad minim veniam.</p>
    <p>Lorem hendrerit in vulputate velit esse molestie consequat, velocity illum dolore eu feugiat nulla facilisis at vero eros et accumsan etlict iusto odio dignissim qui blandit praesent luptatum zzril delenit loei augue duis dolore te feugait nulla facilisi.</p>
  </div>
  <div class="btn btn-blue">Contact Us Today</div>
</section>

<section class="abs programs">
  <h2 class="section-title programs-title">OUR PROGRAMS ALSO PROVIDE<br>STUDENTS THE OPPORTUNITY TO:</h2>
  <div class="rule rule-blue"></div>
  <ul class="programs-list">
    <li><svg width="14" height="12" viewBox="0 0 14 12"><path d="M1 6h10M7 2l4 4-4 4" fill="none" stroke="#2196f3" stroke-width="1.6"/></svg>Participate in large-scale performances.</li>
    <li><svg width="14" height="12" viewBox="0 0 14 12"><path d="M1 6h10M7 2l4 4-4 4" fill="none" stroke="#2196f3" stroke-width="1.6"/></svg>Perform at Linden’s many community events on a regular basis.</li>
    <li><svg width="14" height="12" viewBox="0 0 14 12"><path d="M1 6h10M7 2l4 4-4 4" fill="none" stroke="#2196f3" stroke-width="1.6"/></svg>Access the GTA’s coolest Broadcast stage</li>
    <li><svg width="14" height="12" viewBox="0 0 14 12"><path d="M1 6h10M7 2l4 4-4 4" fill="none" stroke="#2196f3" stroke-width="1.6"/></svg>Attend Clinics, Masterclasses, and Jam Nights</li>
    <li><svg width="14" height="12" viewBox="0 0 14 12"><path d="M1 6h10M7 2l4 4-4 4" fill="none" stroke="#2196f3" stroke-width="1.6"/></svg>Access the Linden Rocks band program. Linden’s Band Program empowers and electrifies students to come together, create music and confidently hit the stage with their own band identity while having fun and honing their instrument.</li>
    <li><svg width="14" height="12" viewBox="0 0 14 12"><path d="M1 6h10M7 2l4 4-4 4" fill="none" stroke="#2196f3" stroke-width="1.6"/></svg>Register in our elite teaching program to learn how to pass on the magic and passion of playing the piano to students.</li>
  </ul>
  <div class="btn btn-blue">Contact Us Today</div>
</section>
<div class="blue-bar" style="left:597px;top:1715px;height:350px"></div>
<div class="abs programs-photo" role="img" aria-label="Photo of a girl playing piano in a group music class with violin students"></div>

<section>
  <div class="abs franchise" role="img" aria-label="Faint background photo of piano keys"></div>
  <h2 class="abs section-title franchise-title">FRANCHISE OPPORTUNITIES</h2>
  <div class="rule abs rule-gold" style="left:584px;top:2346px"></div>
  <p class="abs franchise-sub">Be Part Of The Linden Conservatory Family</p>
  <div class="btn abs btn-gold" style="left:542px;top:2400px;width:115px;height:34px">READ MORE</div>
</section>

<section>
  <div class="abs booking-top" role="img" aria-label="Dark close-up photo of piano keys"></div>
  <div class="abs booking-bottom"></div>
  <h2 class="abs booking-title">BOOK A MEETING WITH US</h2>
  <div class="rule abs rule-gold" style="left:584px;top:2608px"></div>
  <form class="abs form-card">
    <div class="field" style="left:47px;top:33px;width:267px;height:36px">Your Name*</div>
    <div class="field" style="left:324px;top:33px;width:268px;height:36px">Your Phone*</div>
    <div class="field" style="left:604px;top:33px;width:268px;height:36px">Your Email*</div>
    <div class="field" style="left:47px;top:86px;width:825px;height:85px">Your Message*</div>
    <div class="btn abs btn-gold" style="left:401px;top:200px;width:115px;height:34px;font-size:13px">SUBMIT</div>
  </form>
</section>

<footer class="abs contact-strip"></footer>
<div class="contact-item" style="left:107px">
  <svg width="44" height="44" viewBox="0 0 24 24"><path d="M6.6 10.8a15 15 0 0 0 6.6 6.6l2.2-2.2a1 1 0 0 1 1-.25 11.4 11.4 0 0 0 3.6.57 1 1 0 0 1 1 1V20a1 1 0 0 1-1 1A17 17 0 0 1 3 4a1 1 0 0 1 1-1h3.5a1 1 0 0 1 1 1c0 1.25.2 2.45.57 3.57a1 1 0 0 1-.25 1z" fill="#111"/><path d="M14 3a7 7 0 0 1 7 7M14 6.5a3.5 3.5 0 0 1 3.5 3.5" fill="none" stroke="#111" stroke-width="1.6"/></svg>
  <div class="contact-label">CALL US</div>
  <div class="contact-text">1-888-555-0142</div>
</div>
<div class="contact-item" style="left:450px;top:3032px">
  <svg width="36" height="50" viewBox="0 0 24 34"><path d="M12 0a12 12 0 0 0-12 12c0 9 12 22 12 22s12-13 12-22A12 12 0 0 0 12 0zm0 17a5 5 0 1 1 0-10 5 5 0 0 1 0 10z" fill="#111"/></svg>
  <div class="contact-label">POSTAL ADDRESS</div>
  <div class="contact-text">123, Lorem ipsum dolor sit 123456<br>#123456 Lorem ipsum</div>
</div>
<div class="contact-item" style="left:760px;top:3046px">
  <svg width="46" height="34" viewBox="0 0 46 34"><rect x="0" y="0" width="46" height="34" rx="2" fill="#111"/><path d="M3 4l20 15L43 4" fill="none" stroke="#ecc967" stroke-width="2.5"/></svg>
  <div class="contact-label">E-MAIL</div>
  <div class="contact-text">info@chordslinden.example</div>
</div>

</body>
</html>
```